Los Brava Dip – CPG Website with WordPress - Store Locator: WP Maps plugin

Larkfield Food Company is a startup consumer packaged goods (CPG) brand launching its flagship product line — Los Brava Dip. We’re seeking a talented web designer to create a bold, professional, mobile-optimized website using WordPress with a WP Maps store locator to help customers find local retailers.

Our goal is to build a strong online presence that supports both retail growth and direct-to-consumer sales.

See Los Brava _Website_Design_Brief word document.

The website URL is https://losbravadip.example/

Target Market(s)

Consumers of gourmet salsa

Industry/Entity Type

Consumer Packaged Goods - Salsa manufacturer.

Coding

Coded - Design and coding required

Number of Pages Required

5+ page

Requirements
Must have
• The design of the Los Brava Dip website shall emulate the clean, polished aesthetic of Fennigo.example.

```html
<!DOCTYPE html>
<html lang="en">
<head>
<meta charset="utf-8">
<title>Privacy Policy – Los Brava Dip</title>
<link rel="stylesheet" href="https://fonts.googleapis.com/css2?family=Outfit:wght@400;500;600;700&family=Oswald:wght@600;700&display=swap">
<style>
:root{
  --red:#d3262b;
  --brand-red:#c8242b;
  --ink:#1e1e1e;
  --white:#ffffff;
  --green:#1f3a18;
  --green-line:#3f5a35;
  --footer-text:#e9eee6;
  --hero-dark:#7a1608;
  --hero-mid:#d9480f;
  --hero-warm:#f39a1d;
  --hero-gold:#f7c23a;
}
*{box-sizing:border-box;margin:0;padding:0}
html,body{width:707px;height:1200px;overflow:hidden;background:var(--white)}
body{font-family:"Outfit",sans-serif;color:var(--ink);position:relative}

.site-header{position:absolute;top:0;left:0;width:707px;height:46px;background:var(--white);display:flex;align-items:center;padding:0 40px 0 36px;z-index:2}
.brand-name{font-weight:700;font-size:24px;color:var(--brand-red);letter-spacing:-.3px}
.main-nav{margin-left:auto;display:flex;align-items:center;gap:26px}
.main-nav a{font-size:9px;font-weight:600;letter-spacing:.6px;color:var(--ink);text-decoration:none}
.main-nav .contact-btn{background:var(--red);color:var(--white);border-radius:12px;padding:6px 13px}

.hero{position:absolute;top:46px;left:0;width:707px;height:198px;overflow:hidden}
.hero-art{position:absolute;inset:0;background:
  radial-gradient(ellipse 260px 220px at 560px 120px,var(--hero-mid) 0%,rgba(217,72,15,0) 70%),
  radial-gradient(ellipse 200px 160px at 130px 40px,var(--hero-gold) 0%,rgba(247,194,58,0) 75%),
  linear-gradient(100deg,var(--hero-warm) 0%,var(--hero-mid) 45%,var(--hero-dark) 100%)}
.hero-title{position:absolute;top:56px;left:0;width:100%;text-align:center;font-family:"Oswald",sans-serif;font-weight:700;font-size:40px;letter-spacing:1px;color:var(--white)}

.policy{position:absolute;top:282px;left:59px;width:612px;font-size:11px;line-height:16px}
.policy p{margin-bottom:16px}
.policy h2{font-size:11px;font-weight:700;line-height:16px}
.policy h2.plain{font-weight:400}
.policy ul{list-style:none}
.policy li::before{content:"•";display:inline-block;width:12px}
.policy section{margin-bottom:16px}
.effective{font-weight:700}

.site-footer{position:absolute;top:1072px;left:0;width:707px;height:128px;background:var(--green);color:var(--footer-text)}
.footer-brand{position:absolute;top:34px;left:44px;font-weight:700;font-size:26px;color:var(--brand-red)}
.footer-nav{position:absolute;top:46px;left:206px;display:flex;gap:30px}
.footer-nav a{font-size:8.5px;font-weight:500;letter-spacing:.6px;color:var(--footer-text);text-decoration:none}
.footer-rule{position:absolute;top:70px;left:206px;width:456px;height:1px;background:var(--green-line)}
.footer-bottom{position:absolute;top:84px;left:206px;width:456px;display:flex;align-items:center;font-size:7.5px}
.social{display:flex;gap:6px;margin-left:68px}
.social span{width:14px;height:14px;border-radius:50%;background:var(--footer-text);display:block}
.legal{margin-left:16px;display:flex;gap:14px}
.legal a{color:var(--footer-text);text-decoration:none}
</style>
</head>
<body>
<header class="site-header">
  <div class="brand-name">Los Brava</div>
  <nav class="main-nav">
    <a href="#">ABOUT</a><a href="#">PRODUCTS</a><a href="#">WHERE TO BUY</a><a href="#">RECIPES</a><a href="#">REVIEWS</a><a href="#" class="contact-btn">CONTACT ›</a>
  </nav>
</header>

<section class="hero">
  <div class="hero-art" role="img" aria-label="Abstract illustration of warm orange, red and gold pepper-like shapes"></div>
  <h1 class="hero-title">PRIVACY POLICY</h1>
</section>

<main class="policy">
  <p class="effective">Effective Date: June 2025</p>
  <p>At Los Brava Dip, we respect your privacy and are committed to transparency about how we collect and use data on our website, www.losbravadip.example.</p>
  <section>
    <h2 class="plain">1. Information We Collect</h2>
    We do not collect any personal information such as names, emails, or payment details.<br>
    The only data we collect is through cookies, which track general website usage.
  </section>
  <section>
    <h2>2. How We Collect Data</h2>
    We use cookies to collect anonymous usage data when you visit our site. This data may include:
    <ul><li>Browser type</li><li>Device type</li><li>Pages visited</li><li>Time spent on the site</li><li>Referral sources</li></ul>
    This data is collected via tools like Metricly Analytics.
  </section>
  <section>
    <h2>3. How We Use Your Information</h2>
    We use this anonymous usage data strictly to:
    <ul><li>Improve our website's performance</li><li>Understand how users interact with our content</li><li>Enhance the overall user experience</li></ul>
    We do not sell, share, or disclose this data to any third parties.
  </section>
  <section>
    <h2>4. Cookies and Tracking</h2>
    We use cookies to better understand visitor behavior. You can disable cookies through your browser settings if you prefer not to be tracked.
  </section>
  <section>
    <h2>5. Your Rights</h2>
    While we do not collect personally identifiable information, you may contact us at any time to inquire about or request the removal of usage data associated with your visit (support@losbravadip.example).
  </section>
  <section>
    <h2>6. Data Security</h2>
    We protect all collected data using industry-standard security measures, including SSL encryption.
  </section>
  <section>
    <h2>7. Policy Updates</h2>
    This Privacy Policy may be updated from time to time. Any changes will be posted on this page with an updated effective date.
  </section>
  <section>
    <h2>8. Contact Us</h2>
    If you have any questions or concerns about this policy, please contact us at:<br>
    support@losbravadip.example
  </section>
</main>

<footer class="site-footer">
  <div class="footer-brand">Los Brava</div>
  <nav class="footer-nav">
    <a href="#">ABOUT</a><a href="#">PRODUCTS</a><a href="#">WHERE TO BUY</a><a href="#">RECIPES</a><a href="#">REVIEWS</a><a href="#">CONTACT</a>
  </nav>
  <div class="footer-rule"></div>
  <div class="footer-bottom">
    <span>© 2025 Larkfield Food Company. All rights reserved.</span>
    <div class="social"><span></span><span></span></div>
    <div class="legal"><a href="#">Privacy Policy</a><a href="#">Terms of Use</a></div>
  </div>
</footer>
</body>
</html>
```